Design for the A4 Letterhead, envelope and A4 Folder

Design have to be clean, professional, unique (eye catchy) and high end.
Colors: Yellow (Code: 803C), Darker Grey and Black or white (optional)
Logo can be in white or black

Letterhead:
Contain: 1. Korvane Logo
2. Slogan "MADE WITH PRIDE"
3. Company information:
Korvane Valves Pte. Ltd. (Singapore)
Registration no: 201947215K
Tel: (65) 6418 2904
Fax: (65) 6472 9186
Email: sales@korvanevalves.example
Website: http://www.korvanevalves.example
4. Logo watermark

Envelope:
Contain: 1. Korvane Logo
3. website: http://www.korvanevalves.example and email address:
sales@korvanevalves.example
4. Logo watermark

Folder:
Contain: 1. Korvane Logo
3. Company's information:
Tel: (65) 6418 2904
Fax: (65) 6472 9186
4. QR Code
5. Logo watermark
6. On the inside there is a space to insert business card. Contrast colors
between the inside and cover.
Updates

For the Folder design, please be informed that we would prefer to have the Korvane logo on the left hand side of the cover page, rather than on the right hand side.And also if we could highlight the "Made with Pride" slogan with either the yellow box or black/grey box depending on the background color.For the Envelope design,it does not matter where the position of the logo is. But please also highlight the "Made with Pride" Slogan For the Letterhead design, the position of the logo must be on the left hand side and the slogan must be highlighted. In addition, please include the following company information (only for the letterhead design)Korvane Valves Pte. Ltd. (Singapore)Registration no: 200308878MTel: (65) 6535 3735Fax: (65) 6533 3570Email: sales@dynatechpumps.comWebsite: http://www.korvanevalves.example Added Wednesday, August 2, 2017

Target Market(s)

Business to Business, High End market

Industry/Entity Type

It Professional

Font styles to use
Serif

Requirements
Must have
• Design have to be clean, professional, unique (eye catchy) and high end.
Nice to have
• color contrast but still maintaining the professionalism and the seriousness
Should not have
• Messy look, futuristic look, too crowded

```html
<!DOCTYPE html>
<html lang="en">
<head>
<meta charset="utf-8">
<title>Korvane Valves Letterhead</title>
<link rel="stylesheet" href="https://fonts.googleapis.com/css2?family=Open+Sans:wght@400;700&family=Oswald:wght@500&family=Lobster&display=swap">
<style>
  :root {
    --paper: #f5f4f2;
    --ink: #5a5a5a;
    --ink-dark: #58595b;
    --brand-yellow: #ffff00;
    --white: #ffffff;
  }
  html, body {
    margin: 0;
    padding: 0;
    width: 856px;
    height: 1200px;
    overflow: hidden;
    background: var(--paper);
  }
  .letterhead {
    position: relative;
    width: 856px;
    height: 1200px;
    background: var(--paper);
    font-family: "Open Sans", Arial, sans-serif;
    color: var(--ink);
  }
  .accent-bar {
    position: absolute;
    left: 0;
    top: 35px;
    width: 11px;
    height: 133px;
    background: var(--brand-yellow);
  }
  .brand {
    position: absolute;
    left: 58px;
    top: 32px;
    width: 140px;
    text-align: center;
  }
  .brand-circle {
    display: block;
    width: 78px;
    height: 78px;
    margin: 0 auto 8px;
    border-radius: 50%;
    border: 7px solid var(--ink);
    box-sizing: border-box;
  }
  .brand-name {
    font-family: "Oswald", "Arial Narrow", sans-serif;
    font-weight: 500;
    font-size: 34px;
    line-height: 40px;
    letter-spacing: 1px;
    color: var(--ink);
  }
  .contact {
    position: absolute;
    right: 58px;
    top: 34px;
    margin: 0;
    padding: 0;
    list-style: none;
    text-align: right;
    font-size: 14px;
    line-height: 19.5px;
  }
  .contact li {
    display: flex;
    justify-content: flex-end;
    align-items: center;
    gap: 8px;
  }
  .contact .plain { padding-right: 20px; }
  .contact svg {
    width: 12px;
    height: 12px;
    fill: var(--ink);
    flex: none;
  }
  .footer-band {
    position: absolute;
    left: 0;
    top: 1156px;
    width: 856px;
    height: 28px;
  }
  .footer-yellow {
    position: absolute;
    left: 0;
    top: 0;
    width: 650px;
    height: 28px;
    background: var(--brand-yellow);
  }
  .footer-grey {
    position: absolute;
    left: 650px;
    top: 1px;
    width: 206px;
    height: 26px;
    background: var(--ink-dark);
  }
  .slogan {
    position: absolute;
    left: 260px;
    width: 200px;
    top: 0;
    line-height: 28px;
    text-align: center;
    font-family: "Lobster", cursive;
    font-size: 19px;
    color: var(--ink);
  }
  .footer-circle {
    position: absolute;
    left: 627px;
    top: -3px;
    width: 34px;
    height: 34px;
    border-radius: 50%;
    background: var(--white);
    border: 2px solid var(--ink-dark);
    box-sizing: border-box;
  }
</style>
</head>
<body>
  <main class="letterhead">
    <div class="accent-bar"></div>

    <div class="brand">
      <span class="brand-circle"></span>
      <div class="brand-name">KORVANE</div>
    </div>

    <ul class="contact">
      <li class="plain">Korvane Valves Pte. Ltd.</li>
      <li class="plain">412 Calderwood Road #05-12B</li>
      <li class="plain">Singapore 574318</li>
      <li>(65) 6418 2904
        <svg viewBox="0 0 12 12" aria-hidden="true"><path d="M2.2 0.8l2 2.1-1 1.3c.7 1.6 1.9 2.8 3.5 3.6l1.3-1 2.2 2-1 2c-4.6-.4-8.3-4.1-8.7-8.7z"/></svg>
      </li>
      <li>(65) 6472 9186
        <svg viewBox="0 0 12 12" aria-hidden="true"><path d="M3 1h5l1 1v2H3zM1 5h10v5H9V8H3v2H1zM3.5 9h5v2.5h-5z"/></svg>
      </li>
      <li>sales@korvanevalves.example
        <svg viewBox="0 0 12 12" aria-hidden="true"><path d="M1 2.5h10v1L6 6.5 1 3.5zM1 5l5 3 5-3v4.5H1z"/></svg>
      </li>
      <li>www.korvanevalves.example
        <svg viewBox="0 0 12 12" aria-hidden="true"><path d="M6 .5a5.5 5.5 0 1 0 0 11A5.5 5.5 0 0 0 6 .5zm-1 2.2c1 .3 1.6 1.2 1.2 2-.4.7-1.6.5-1.9 1.4-.2.8.9 1.5.4 2.6C3 8 2.2 6.4 2.4 4.9 2.9 3.6 3.9 2.7 5 2.7zm3 3.6c.9-.2 1.6.4 1.5 1.3-.3 1-1.2 1.9-2.3 2.2.4-1.2-.4-3.3.8-3.5z"/></svg>
      </li>
    </ul>

    <div class="footer-band">
      <div class="footer-yellow"></div>
      <div class="footer-grey"></div>
      <div class="slogan">Made With Pride</div>
      <div class="footer-circle"></div>
    </div>
  </main>
</body>
</html>
```